Diverse, up-scale salon needs eye-catching, unique business cards.

We are looking for a unique business card design for our stylist but that can also be multi functional and used for appointment reminder and referrals. I will need a design in a format that I can modify names and titles going forward. In the past we have had a dark background with the logo on one side, and stylist and contact information on the other but we are open to all ideas. I have included our mission statement as well as branded colors below. The statement doesn't need to go on the card, it's just a reference for target market. We need space for the stylists name, title, instagram handle and then the salons phone number, website and address. I am also open to adding a spot for a qr code linked to the stylist instagram or the salon booking link.

primary brand colors:
#333333 #233415 #36502a #93874a #000000
Mission statement:
Vessolin Hair Studio, a high-end salon located in the lively Downtown Farmington, Michigan, is committed to providing exceptional services in a welcoming and relaxed environment to meet the needs of our diverse clientele.
Our salon specializes in contemporary custom haircuts, coloring, extensions, and barbering and beard grooming services. Our team of skilled stylists is passionate and inventive in their hair styling techniques. At the heart of our salon are values centered on quality, innovation, creativity, and above all, comfort. These core values are evident in every appointment across our customizable array of services.
Our goal is to establish a benchmark for exceptional hair care for every human.
Website: www.vessolinhairstudio.example
instagram: @vessolinhairstudio
address: 41782 Pelham Crest Rd, Farmington MI
phone: 248-613-4087

Industry/Entity Type

Hair Salon

Contact Information for Business Card

Stylist name, title, phone, instagram, website, address, (optional qr code)

Requirements
Should not have
• Does not need mission statement on the card.

```html
<!DOCTYPE html>
<html lang="en">
<head>
<meta charset="utf-8">
<title>Vessolin Hair Studio – Business Card</title>
<link href="https://fonts.googleapis.com/css2?family=Kaushan+Script&family=Poppins:wght@300;400;600&display=swap" rel="stylesheet">
<style>
  :root {
    --backdrop: #cccccc;
    --card-dark: #1f1f1f;
    --gold: #a89c5c;
    --gold-deep: #978a4e;
    --gold-light: #cdbb6b;
    --ink: #111111;
    --white: #ffffff;
  }
  * { margin: 0; padding: 0; box-sizing: border-box; }
  html, body { width: 1200px; height: 900px; overflow: hidden; }
  body { background: var(--backdrop); position: relative; font-family: "Poppins", sans-serif; }

  .card { position: absolute; width: 604px; height: 346px; overflow: hidden; }
  .card--front { left: 162px; top: 89px; }
  .card--back { left: 450px; top: 478px; background: var(--card-dark); }

  /* Front – header band */
  .header-band { position: absolute; left: 0; top: 0; width: 604px; height: 143px; background: var(--card-dark); }
  .header-art {
    position: absolute; right: 0; top: 0; width: 178px; height: 143px;
    background: radial-gradient(ellipse at 60% 50%, #2a2924 0%, var(--card-dark) 75%);
  }
  .stylist-name { position: absolute; left: 49px; top: 30px; white-space: nowrap; }
  .stylist-name__first {
    font-family: "Poppins", sans-serif; font-weight: 300; font-size: 56px;
    color: var(--gold); letter-spacing: -0.5px; vertical-align: baseline;
  }
  .stylist-name__last {
    font-family: "Kaushan Script", cursive; font-size: 50px; color: var(--white);
    margin-left: 14px; vertical-align: baseline;
  }
  .salon-line {
    position: absolute; left: 50px; top: 104px; font-size: 13px; font-weight: 600;
    letter-spacing: 4px; color: var(--gold);
  }

  /* Front – gold contact band */
  .contact-band {
    position: absolute; left: 0; top: 143px; width: 604px; height: 203px;
    background: linear-gradient(90deg, var(--gold-deep) 0%, #b9aa61 25%, var(--gold-light) 50%, #b9aa61 75%, var(--gold-deep) 100%);
  }
  .contact-item { position: absolute; top: 35px; text-align: center; color: var(--ink); font-size: 16px; line-height: 20px; white-space: nowrap; }
  .contact-item svg { display: block; margin: 0 auto 6px; }
  .contact-item--phone { left: 8px; width: 200px; }
  .contact-item--address { left: 188px; width: 220px; }
  .contact-item--social { left: 412px; width: 190px; font-size: 15px; }
  .divider { position: absolute; top: 62px; width: 1px; height: 40px; background: rgba(255,255,255,0.75); }
  .divider--one { left: 184px; }
  .divider--two { left: 410px; }
  .web-front {
    position: absolute; left: 0; width: 604px; top: 144px; text-align: center;
    color: var(--white); font-weight: 600; font-size: 16px; letter-spacing: 3px;
  }

  /* Back */
  .brand-mark { position: absolute; left: 229px; top: 96px; width: 136px; height: 136px; }
  .brand-mark__name {
    position: absolute; inset: 0; display: flex; align-items: center; justify-content: center;
    text-align: center; color: var(--gold); font-weight: 600; font-size: 14px;
    letter-spacing: 3px; line-height: 20px;
  }
  .web-back {
    position: absolute; left: 0; width: 604px; top: 280px; text-align: center;
    color: var(--gold); font-weight: 300; font-size: 17px; letter-spacing: 3.5px;
  }
</style>
</head>
<body>

<section class="card card--front">
  <div class="header-band">
    <div class="header-art" role="img" aria-label="Faint scissors and comb illustration"></div>
    <h1 class="stylist-name"><span class="stylist-name__first">Delara</span><span class="stylist-name__last">Quint</span></h1>
    <p class="salon-line">VESSOLIN HAIR STUDIO</p>
  </div>

  <div class="contact-band">
    <div class="contact-item contact-item--phone">
      <svg width="14" height="16" viewBox="0 0 24 24" aria-hidden="true"><path fill="#fff" d="M6.6 10.8c1.4 2.8 3.8 5.1 6.6 6.6l2.2-2.2c.3-.3.7-.4 1-.2 1.1.4 2.3.6 3.6.6.6 0 1 .4 1 1V20c0 .6-.4 1-1 1C10.6 21 3 13.4 3 4c0-.6.4-1 1-1h3.5c.6 0 1 .4 1 1 0 1.3.2 2.5.6 3.6.1.3 0 .7-.2 1z"/></svg>
      248-613-4087
    </div>
    <div class="divider divider--one"></div>
    <div class="contact-item contact-item--address">
      <svg width="16" height="20" viewBox="0 0 24 30" aria-hidden="true"><path fill="#fff" d="M12 0C5.4 0 0 5.2 0 11.7 0 20.4 12 30 12 30s12-9.6 12-18.3C24 5.2 18.6 0 12 0zm0 16a4.5 4.5 0 1 1 0-9 4.5 4.5 0 0 1 0 9z"/></svg>
      41782 Pelham Crest Rd,<br>Farmington MI
    </div>
    <div class="divider divider--two"></div>
    <div class="contact-item contact-item--social">
      <svg width="20" height="14" viewBox="0 0 20 14" aria-hidden="true"><rect x="0.5" y="0.5" width="19" height="13" fill="none" stroke="#fff"/><path d="M0.5 0.5 10 8 19.5 0.5M0.5 13.5 7.5 6.5M19.5 13.5 12.5 6.5" fill="none" stroke="#fff"/></svg>
      @vessolinhairstudio
    </div>
    <p class="web-front">www.vessolinhairstudio.example</p>
  </div>
</section>

<section class="card card--back">
  <div class="brand-mark">
    <svg width="136" height="136" viewBox="0 0 136 136" aria-hidden="true"><circle cx="68" cy="68" r="66" fill="none" stroke="var(--gold)" stroke-width="2.5"/></svg>
    <p class="brand-mark__name">VESSOLIN<br>HAIR STUDIO</p>
  </div>
  <p class="web-back">www.vessolinhairstudio.example</p>
</section>

</body>
</html>
```